Kestrel Facilities Business Card Design

We would now like to design business cards with the new Kestrel Facilities logo

Target Market(s)

Professional

Industry/Entity Type

Professional services

Contact Information for Business Card

Employee name, title, phone number, email address, corporate office address and logo.

Font styles to use
Sans Serif

Colors
0054AA
0677BA
7BADD7
CADEEF
E8F1F8

Requirements
Must have
• My logo
Should not have
• any other pictures or images besides my logo

```html
<!DOCTYPE html>
<html lang="en">
<head>
<meta charset="utf-8">
<title>Kestrel Facilities Business Card</title>
<link href="https://fonts.googleapis.com/css2?family=Roboto+Condensed:wght@400;700&family=Arimo:wght@400&display=swap" rel="stylesheet">
<style>
  :root {
    --brand-blue: #0a84e6;
    --brand-blue-deep: #0677ba;
    --paper: #f4f4f4;
    --ink: #1a1a1a;
    --backdrop: #dadada;
  }
  * { margin: 0; padding: 0; box-sizing: border-box; }
  html, body {
    width: 1200px; height: 930px; overflow: hidden;
    background: var(--backdrop);
  }
  .canvas {
    position: relative; width: 1200px; height: 930px;
  }
  .card {
    position: absolute; width: 560px; height: 320px;
    box-shadow: 0 10px 28px rgba(0,0,0,0.14);
    overflow: hidden;
  }
  .card--front {
    left: 560px; top: 110px;
    background: var(--brand-blue);
    display: flex; align-items: center; justify-content: center;
  }
  .card--back {
    left: 80px; top: 500px;
    background: var(--paper);
    display: flex;
  }
  .brand {
    display: flex; align-items: center; gap: 14px;
    font-family: "Roboto Condensed", sans-serif;
    font-weight: 700; color: #ffffff;
    text-transform: uppercase; letter-spacing: 2px;
  }
  .brand__square { width: 26px; height: 26px; background: #ffffff; flex: none; }
  .brand__name { font-size: 40px; line-height: 1; }
  .card--front .brand__name { font-size: 44px; }
  .back__brand-panel {
    width: 48%; height: 100%;
    background: var(--brand-blue);
    display: flex; align-items: center; justify-content: center;
    padding: 20px;
  }
  .back__brand-panel .brand { flex-direction: column; align-items: flex-start; gap: 10px; }
  .back__brand-panel .brand__name { font-size: 34px; line-height: 1.05; }
  .contact {
    flex: 1; padding: 46px 26px 0 28px;
    font-family: "Arimo", sans-serif; color: var(--ink);
  }
  .contact__name {
    font-family: "Roboto Condensed", sans-serif; font-weight: 700;
    color: var(--brand-blue); font-size: 25px; text-transform: uppercase;
    letter-spacing: 0.3px; line-height: 1;
  }
  .contact__title { font-size: 15px; margin-top: 4px; }
  .contact__list { list-style: none; margin-top: 20px; font-size: 15px; line-height: 1.45; }
  .contact__list li { display: flex; align-items: center; gap: 8px; }
  .contact__list svg { width: 14px; height: 14px; flex: none; fill: var(--brand-blue); }
  .contact__web-host { color: var(--brand-blue); }
  .contact__address { margin-top: 18px; font-size: 15px; line-height: 1.35; }
</style>
</head>
<body>
<main class="canvas">
  <section class="card card--front" aria-label="Card front">
    <div class="brand">
      <span class="brand__square"></span>
      <span class="brand__name">Kestrel Facilities</span>
    </div>
  </section>

  <section class="card card--back" aria-label="Card back">
    <div class="back__brand-panel">
      <div class="brand">
        <span class="brand__square"></span>
        <span class="brand__name">Kestrel<br>Facilities</span>
      </div>
    </div>
    <div class="contact">
      <p class="contact__name">Daniel Harper</p>
      <p class="contact__title">Managing Director</p>
      <ul class="contact__list">
        <li>
          <svg viewBox="0 0 24 24" aria-hidden="true"><path d="M6.6 10.8a15.1 15.1 0 0 0 6.6 6.6l2.2-2.2c.3-.3.7-.4 1-.2 1.1.4 2.3.6 3.6.6.6 0 1 .4 1 1V20c0 .6-.4 1-1 1A17 17 0 0 1 3 4c0-.6.4-1 1-1h3.5c.6 0 1 .4 1 1 0 1.3.2 2.5.6 3.6.1.3 0 .7-.2 1z"/></svg>
          044-210 375 648
        </li>
        <li>
          <svg viewBox="0 0 24 24" aria-hidden="true"><path d="M2 5h20v14H2z M2 5l10 8 10-8" fill="none" stroke="#0a84e6" stroke-width="2"/></svg>
          info@kestrelfm.com
        </li>
        <li>
          <svg viewBox="0 0 24 24" aria-hidden="true"><circle cx="12" cy="12" r="10"/></svg>
          <span>www.<span class="contact__web-host">kestrelfm</span>.com</span>
        </li>
      </ul>
      <p class="contact__address">18 Alder Row, Suite 4<br>61830, Northvale</p>
    </div>
  </section>
</main>
</body>
</html>
```